MRT Property - Business Cards

Looking for a business card & general letterhead, signage etc design for our new logo.

Colours:
000a20
0056a2
00b5ef
0088ce
68cef2

Fonts:
Poppins
Karla

Please keep look and feel of new brand - example in the zip package I sent.

```html
<!DOCTYPE html>
<html lang="en">
<head>
<meta charset="utf-8">
<title>MRT Property – Business Cards</title>
<link rel="stylesheet" href="https://fonts.googleapis.com/css2?family=Poppins:wght@500;600;700&family=Karla:wght@400;500&display=swap">
<style>
  :root {
    --ink: #000a20;
    --card-dark: #0f1428;
    --navy: #0056a2;
    --cyan: #00b5ef;
    --mid-blue: #0088ce;
    --sky: #68cef2;
    --paper: #ffffff;
    --stage: #3d3d3d;
    --text-light: #f2f4f8;
  }
  * { box-sizing: border-box; margin: 0; padding: 0; }
  html, body { width: 1200px; height: 803px; overflow: hidden; }
  body {
    background: var(--stage);
    display: flex;
    align-items: center;
    justify-content: center;
    gap: 44px;
  }
  .card {
    position: relative;
    width: 530px;
    height: 303px;
    border-radius: 22px;
    overflow: hidden;
    box-shadow: 0 18px 40px rgba(0,0,0,.45);
  }
  .card--front { background: var(--card-dark); }
  .card--back {
    background: var(--paper);
    display: flex;
    align-items: center;
    justify-content: center;
  }
  .card__accent {
    position: absolute;
    right: 40px;
    top: 34px;
    width: 200px;
    height: 200px;
  }
  .contact {
    position: absolute;
    left: 34px;
    bottom: 28px;
    font-family: "Karla", sans-serif;
    color: var(--text-light);
  }
  .brand-name {
    font-family: "Poppins", sans-serif;
    font-weight: 700;
    color: var(--navy);
    letter-spacing: .5px;
    line-height: 1;
  }
  .contact .brand-name { font-size: 30px; margin-bottom: 12px; }
  .person__name {
    font-family: "Poppins", sans-serif;
    font-weight: 600;
    font-size: 19px;
    color: var(--navy);
    line-height: 1.1;
  }
  .person__role {
    font-size: 12px;
    color: var(--cyan);
    margin-bottom: 10px;
  }
  .address { font-size: 12.5px; line-height: 1.35; margin-bottom: 8px; }
  .details { list-style: none; font-size: 12.5px; line-height: 1.45; }
  .details li { display: flex; align-items: center; gap: 8px; }
  .details svg { width: 10px; height: 10px; flex: none; }
  .back-brand { display: flex; align-items: center; gap: 16px; }
  .back-brand .brand-name { font-size: 52px; }
  .back-brand__dot {
    width: 30px; height: 30px; border-radius: 50%;
    background: var(--mid-blue);
  }
</style>
</head>
<body>
  <section class="card card--front" aria-label="Business card front">
    <svg class="card__accent" viewBox="0 0 200 200" aria-hidden="true">
      <circle cx="100" cy="100" r="96" fill="var(--mid-blue)" opacity=".85"/>
    </svg>
    <div class="contact">
      <div class="brand-name">MRT Property</div>
      <div class="person__name">Dana Whitlow</div>
      <div class="person__role">President</div>
      <p class="address">4120 Alder Crest Road<br>Millbrook, Canada 20918</p>
      <ul class="details">
        <li><svg viewBox="0 0 10 10"><path d="M2 1h2l1 2-1.2 1a5 5 0 0 0 2.2 2.2L7 5l2 1v2c0 .6-.4 1-1 1A8 8 0 0 1 1 2c0-.6.4-1 1-1z" fill="var(--navy)"/></svg>555-214-7730</li>
        <li><svg viewBox="0 0 10 10"><rect x="1.5" y="1.5" width="7" height="7" fill="none" stroke="var(--text-light)" stroke-width="1.2"/></svg>555-382-9146</li>
        <li><svg viewBox="0 0 10 10"><rect x="1" y="2" width="8" height="6" fill="var(--navy)"/><path d="M1 2l4 3 4-3" fill="none" stroke="var(--text-light)" stroke-width=".8"/></svg>info@mrtproperty.com</li>
        <li><svg viewBox="0 0 10 10"><circle cx="5" cy="5" r="4" fill="var(--navy)"/></svg>www.mrtproperty.com</li>
      </ul>
    </div>
  </section>

  <section class="card card--back" aria-label="Business card back">
    <div class="back-brand">
      <span class="back-brand__dot" aria-hidden="true"></span>
      <span class="brand-name">MRT Property</span>
    </div>
  </section>
</body>
</html>
```